Animal Eye Clinic needs a Business card

We are a new veterinary ophthalmology practice (Ridgeline Pet Vision Care) and we need a business card designed. We only see animal eyes - we are not a regular veterinary clinic. We already have a logo. We are looking for a professional, good looking business card to hand out to our clients. We are looking for something simple but professional and contemporary. Our logo is likely the only picture/graphic that needs to be on the card.
Updates

Contact Information for Business Card

Delia Vossman, BSc, DVM, MSc, DipACVO
Veterinary Ophthalmologist

Phone: 250.418.3927
Email: ridgelinepetvisioncare@mailbox-example.net
Website: ridgelinepetvisioncare-example.net
Address: 1874 Thornbury Rd
Kelowna, BC, V1X 4M9

Colors

Designer to choose colors to be used in the design.

Requirements
Must have
• Our logo (attached)

```html
<!DOCTYPE html>
<html lang="en">
<head>
<meta charset="utf-8">
<title>Ridgeline Pet Vision Care – Business Card</title>
<link rel="stylesheet" href="https://fonts.googleapis.com/css2?family=Open+Sans:wght@400;600;700&display=swap">
<style>
  :root {
    --page-bg: #e6e8ea;
    --card-bg: #f7f8f8;
    --teal: #0f95a8;
    --rim: #6f7375;
    --ink-light: #ffffff;
  }
  * { box-sizing: border-box; margin: 0; padding: 0; }
  html, body {
    width: 1200px;
    height: 900px;
    overflow: hidden;
    background: var(--page-bg);
    font-family: "Open Sans", Arial, sans-serif;
  }
  .business-card {
    position: absolute;
    left: 110px;
    top: 148px;
    width: 980px;
    height: 604px;
    background: var(--card-bg);
    box-shadow: 0 10px 30px rgba(0,0,0,0.12);
    overflow: hidden;
  }
  .lens-panel {
    position: absolute;
    inset: 0;
    width: 980px;
    height: 604px;
  }
  .contact-block {
    position: absolute;
    right: 44px;
    top: 104px;
    text-align: right;
    color: var(--ink-light);
  }
  .person-name {
    font-size: 29px;
    font-weight: 700;
    letter-spacing: 0.5px;
    line-height: 1.25;
  }
  .credentials, .role {
    font-size: 22px;
    line-height: 1.7;
  }
  .contact-list {
    list-style: none;
    margin-top: 22px;
    font-size: 22px;
    line-height: 1.7;
  }
  .contact-list li {
    display: flex;
    justify-content: flex-end;
    align-items: center;
    gap: 8px;
  }
  .contact-icon { width: 20px; height: 20px; flex: none; }
  .address {
    margin-top: 26px;
    font-size: 22px;
    line-height: 1.7;
    font-style: normal;
  }
  .brand {
    position: absolute;
    left: 40px;
    top: 496px;
    display: flex;
    align-items: center;
    gap: 16px;
  }
  .brand-dot {
    width: 56px;
    height: 56px;
    border-radius: 50%;
    background: var(--teal);
  }
  .brand-name {
    color: var(--teal);
    font-size: 30px;
    font-weight: 700;
  }
</style>
</head>
<body>
  <div class="business-card">
    <svg class="lens-panel" viewBox="0 0 980 604" aria-hidden="true">
      <path d="M900 0 C 640 60, 460 170, 413 296 C 460 420, 640 545, 900 604 L 980 604 L 980 0 Z"
            fill="var(--teal)" stroke="var(--rim)" stroke-width="5"/>
    </svg>

    <div class="contact-block">
      <h1 class="person-name">DELIA VOSSMAN</h1>
      <p class="credentials">BSC, DVM, MSC, DIPACVO</p>
      <p class="role">Veterinary Ophthalmologist</p>

      <ul class="contact-list">
        <li>250.418.3927
          <svg class="contact-icon" viewBox="0 0 20 20" aria-hidden="true"><path fill="#fff" d="M4 6c0-2 2-3 6-3s6 1 6 3v1h-3V6H7v1H4zM5 9h10l2 7H3z"/><circle cx="10" cy="12.5" r="2" fill="var(--teal)"/></svg>
        </li>
        <li>ridgelinepetvisioncare@mailbox-example.net
          <svg class="contact-icon" viewBox="0 0 20 20" aria-hidden="true"><rect x="2" y="4" width="16" height="12" fill="#fff"/><path d="M2 4l8 7 8-7" fill="none" stroke="var(--teal)" stroke-width="1.6"/></svg>
        </li>
        <li>ridgelinepetvisioncare-example.net
          <svg class="contact-icon" viewBox="0 0 20 20" aria-hidden="true"><circle cx="10" cy="10" r="8" fill="#fff"/><path d="M2 10h16M10 2c-3 3-3 13 0 16M10 2c3 3 3 13 0 16" fill="none" stroke="var(--teal)" stroke-width="1.3"/></svg>
        </li>
      </ul>

      <address class="address">1874 Thornbury Rd<br>Kelowna, BC, V1X 4M9</address>
    </div>

    <div class="brand">
      <span class="brand-dot"></span>
      <span class="brand-name">Ridgeline Pet Vision Care</span>
    </div>
  </div>
</body>
</html>
```